I need a label design to go on our jars of honey. Our company is called Marrowdale Honey Co. The type of honey is called Fernlight Glen Honey. The jars are 1kg. Attached is the label size. Left hand side needs to have nutritional info... as attached. Middle section is our company name, honey type, 1kg & Whangamata, NZ. Right hand side needs to have info as per photo (raw honey etc). I would like to upload more pictures... but I’m unsure how to do this? Thanks, Carla

Target Market(s)

Honey consumers... families

Industry/Entity Type

Food Production

Colors

Designer to choose colors to be used in the design.

Requirements
Must have
• Nutritional info as per upload
• Type of honey & company name as per upload
• 1kg
• Address
Nice to have
• Similar fonts to upload.
• Possibly background image... floral or beach... very faint though.

```html
<!DOCTYPE html>
<html lang="en">
<head>
<meta charset="utf-8">
<title>Marrowdale Honey Co. – Jar Label, Right Panel</title>
<link href="https://fonts.googleapis.com/css2?family=Inter:wght@300&display=swap" rel="stylesheet">
<style>
  :root {
    --bg-deep: #1b1913;
    --bg-warm: #231f18;
    --bloom-core: #4e2e1c;
    --bloom-mid: #3a261a;
    --ink: #fbf8f2;
  }
  html, body {
    margin: 0;
    padding: 0;
    width: 1200px;
    height: 1200px;
    overflow: hidden;
    background: var(--bg-deep);
  }
  .label-panel {
    position: relative;
    width: 1200px;
    height: 1200px;
    overflow: hidden;
    background: radial-gradient(ellipse at 60% 40%, var(--bg-warm) 0%, var(--bg-deep) 75%);
    font-family: "Inter", "Helvetica Neue", Arial, sans-serif;
    color: var(--ink);
  }
  .floral-backdrop {
    position: absolute;
    left: -380px;
    top: 170px;
    width: 620px;
    height: 920px;
    border-radius: 50%;
    background: radial-gradient(ellipse at 58% 50%, var(--bloom-core) 0%, var(--bloom-mid) 50%, rgba(35, 28, 20, 0) 75%);
    filter: blur(14px);
    opacity: 0.8;
  }
  .copy-block {
    position: absolute;
    left: 374px;
    width: 720px;
    text-align: center;
    font-weight: 300;
    font-size: 40px;
    line-height: 52px;
    letter-spacing: -0.3px;
    margin: 0;
  }
  .origin { top: 92px; }
  .raw-note { top: 246px; }
  .sign-off { top: 456px; }
  .blessing { top: 612px; }
  .contact { top: 872px; }
  .divider {
    position: absolute;
    left: 456px;
    top: 835px;
    width: 558px;
    height: 6px;
    background: var(--ink);
  }
</style>
</head>
<body>
  <main class="label-panel">
    <div class="floral-backdrop" role="img" aria-label="Faint blurred photograph of a warm orange flower"></div>

    <p class="copy-block origin">Sourced from the beautiful<br>Coromandel Peninsula.</p>
    <p class="copy-block raw-note">Our honey comes to you raw &amp;<br>unpasteurised, ensuring it retains all<br>natural goodness!</p>
    <p class="copy-block sign-off">Arohanui,<br>Rowan, Carla &amp; boys</p>
    <p class="copy-block blessing">‘Marrowdale’ all thanks to God for His<br>incredible creation!</p>

    <div class="divider"></div>

    <p class="copy-block contact">www.marrowdalehoney.co.nz<br>42 Kereru Lane<br>Whangamata, New Zealand</p>
  </main>
</body>
</html>
```